Harborview Estates Business Card for Apartment Buildings

Create business cards for resident managers who run apartment buildings. The audience is the public who are searching for apartment rentals, and current residents who live at the apartment building. Key design element will be incorporating the company logo, however, the logo cannot dominate. The building name and manager name are more important than the logo. Current business card design leaves little room for copy, so we may need to reduce the size on the current card to allow for more space for copy.

Target Market(s)

Adults 18-65 years of age, who are looking for an apartment rental, plus current residents who live at our apartment buildings.

Industry/Entity Type

Property Management

Contact Information for Business Card

A major design element will be use of the company logo. Important property and manager contact information must be part of the design. The size of the logo will need to be reduced to make room for building and manager contact copy.

Font styles to use
Sans Serif

Colors
3176b5
000000
959595
ffffff

Requirements
Must have
• 1) Incorporate the company logo.
• 2) Use the company colors (dark blue, black/grey, over white).
• 3) FEATURE THE BUILDING NAME
• 4) FEATURE THE MANAGER NAME
• 5) The company name is less important than BUILDING and MANAGER
• 6) Manager contact information
• **SEE ATTACHED CREATIVE BRIEF**
Nice to have
• 1) Back of card logo watermark
• 2) Ability to write notes on back of carfd
Should not have
• Avoid letting the company logo dominate the card, the building name and manager are more important than the company logo.

```html
<!DOCTYPE html>
<html lang="en">
<head>
<meta charset="utf-8">
<title>Cedar Court Apartments – Business Card</title>
<link href="https://fonts.googleapis.com/css2?family=Lato:wght@400;700;900&display=swap" rel="stylesheet">
<style>
  :root {
    --brand-blue: #3176b5;
    --ink: #1f1f21;
    --band-dark: #45464a;
    --mid-grey: #959595;
    --paper: #ffffff;
    --paper-soft: #f8f9fb;
    --watermark: #e7e9ee;
    --stage: #8f9596;
  }
  * { margin: 0; padding: 0; box-sizing: border-box; }
  html, body { width: 1200px; height: 1000px; overflow: hidden; }
  body {
    background: var(--stage);
    font-family: "Lato", Arial, sans-serif;
    position: relative;
  }
  .card {
    position: absolute;
    background: var(--paper);
    overflow: hidden;
    box-shadow: 0 4px 14px rgba(0,0,0,0.25);
  }
  .card-front { left: 40px; top: 311px; width: 660px; height: 377px; }
  .card-back { left: 770px; top: 170px; width: 377px; height: 660px; background: var(--paper-soft); }
  .card-shapes { position: absolute; inset: 0; }

  .building-name { position: absolute; color: var(--ink); line-height: 1; }
  .building-name .title { display: block; font-weight: 900; letter-spacing: -0.5px; }
  .building-name .subtitle { display: block; font-weight: 700; text-transform: uppercase; }
  .card-front .building-name { left: 262px; top: 30px; }
  .card-front .building-name .title { font-size: 46px; }
  .card-front .building-name .subtitle { font-size: 19px; letter-spacing: 10.5px; margin-top: 6px; padding-left: 2px; }

  .address { position: absolute; left: 200px; top: 150px; font-size: 14px; color: var(--ink); }
  .address .sep { color: var(--mid-grey); margin: 0 6px; }

  .manager-name {
    position: absolute; left: 34px; top: 213px;
    color: var(--paper); font-weight: 900; font-size: 29px; letter-spacing: 0.5px; text-transform: uppercase;
  }
  .manager-role {
    position: absolute; left: 80px; top: 263px;
    color: var(--paper); font-weight: 700; font-size: 18px;
  }
  .contact {
    position: absolute; right: 46px; top: 190px;
    text-align: right; color: var(--ink); font-size: 18px; line-height: 1.3; list-style: none;
  }
  .company-name {
    position: absolute; left: 40px; top: 325px;
    color: var(--brand-blue); font-weight: 900; font-size: 17px;
  }

  .card-back .building-name { left: 42px; top: 42px; }
  .card-back .building-name .title { font-size: 42px; }
  .card-back .building-name .subtitle { font-size: 18px; letter-spacing: 9.5px; margin-top: 6px; padding-left: 14px; }
</style>
</head>
<body>

  <section class="card card-front" aria-label="Business card front">
    <svg class="card-shapes" width="660" height="377" viewBox="0 0 660 377" aria-hidden="true">
      <rect x="0" y="0" width="660" height="130" fill="#fdfdfd"/>
      <rect x="0" y="130" width="660" height="3" fill="#ececec"/>
      <polygon points="0,100 70,100 70,300 0,300" fill="var(--brand-blue)"/>
      <rect x="255" y="122" width="395" height="4" fill="var(--brand-blue)"/>
      <polygon points="0,208 435,208 395,258 0,258" fill="var(--band-dark)"/>
      <polygon points="0,258 260,258 235,292 0,292" fill="var(--brand-blue)"/>
      <circle cx="112" cy="152" r="62" fill="var(--paper)"/>
      <circle cx="112" cy="152" r="46" fill="none" stroke="#d9d9d9" stroke-width="8"/>
      <line x1="70" y1="185" x2="600" y2="185" stroke="var(--brand-blue)" stroke-width="0" />
    </svg>

    <h1 class="building-name">
      <span class="title">Cedar Court</span>
      <span class="subtitle">Apartments</span>
    </h1>
    <p class="address">2480 Linden Avenue<span class="sep">|</span>Bayside, CA 90210</p>
    <h2 class="manager-name">Marisol Ortega</h2>
    <p class="manager-role">Resident Manager</p>
    <ul class="contact">
      <li>Office: 555-210-4400</li>
      <li>Fax: 555-210-4401</li>
      <li>Cell: 555-384-9102</li>
      <li>Email: marisol@harborviewest.com</li>
    </ul>
    <p class="company-name">Harborview Estates</p>
  </section>

  <section class="card card-back" aria-label="Business card back">
    <svg class="card-shapes" width="377" height="660" viewBox="0 0 377 660" aria-hidden="true">
      <rect x="0" y="0" width="377" height="150" fill="var(--paper)"/>
      <polygon points="0,150 377,120 377,136 0,166" fill="var(--brand-blue)"/>
      <circle cx="260" cy="360" r="200" fill="none" stroke="var(--watermark)" stroke-width="18"/>
    </svg>
    <h1 class="building-name">
      <span class="title">Cedar Court</span>
      <span class="subtitle">Apartments</span>
    </h1>
  </section>

</body>
</html>
```